Book cover for "Steady Harbor" focused on scaling up an Insurance Agency

Front Cover:
We need book cover for our upcoming book with title "Steady Harbor" . Subtitle of book is "The secrets behind building a multi-million dollar Insurance agency:Interviews, success stories and framework for success".
On top line it should say " Foreword by Milo Venhart".
Author name : "Rudrank Bhalotia"
This book will help insurance agents in scaling up their agency. It will also help someone looking to start a business or side hustle.

Back Cover:
It should contain content provided below and image of author attached.
"
Who should read this book?

Do you know that starting an Insurance Agency is probably one of the best business ideas?
Do you want to know how some startups created billion dollar plus insurance based companies in the last 5-10 years?
Do you want to know the secrets behind building a multi-million dollar Insurance agency?
Do you want to know how to scale up an Insurance Agency profitably?
Do you want to know how to cut through the noise in the market and differentiate your business?
How to leverage technology to rise above (be seen and heard) the myriad of agencies around you and compete with both local and online agencies?
How to build a team which carries your mindset to take care of clients and grow your business?
(above list should be bulleted)
If you are interested in learning about these topics then you are at the right place.

You can either spend years figuring out things yourself or read this book and get wisdom from successful agents and thought leaders at top insurance agencies."

Spine:
" Steady Harbor by Rudrank Bhalotia"

Requirements:
One file should be only book cover.
Other file should contain :front cover, back cover and spine as one file.
It should follow standard for Lumora QPS, link provided below.
https://qps.lumorabooks.example/en_US/help/topic/H847362159

Target Market(s)

Insurance Agents
People looking to start a new business
Side Hustlers

Industry/Entity Type

Insurance Agency

Font styles to use
Serif

```html
<!DOCTYPE html>
<html lang="en">
<head>
<meta charset="utf-8">
<title>Steady Harbor – Full Cover Wrap</title>
<link rel="stylesheet" href="https://fonts.googleapis.com/css2?family=Roboto+Condensed:wght@400;500;700;900&family=Roboto:wght@300;400&family=Source+Sans+3:wght@400;600;700&display=swap">
<style>
  :root{
    --paper:#d9dadc;
    --band:#ededed;
    --ink:#1f1f20;
    --accent-blue:#2a5fa6;
    --spine-blue:#3a6bb0;
    --rule:#8d8e90;
    --frame:#ffffff;
    --sky-top:#2b63a9;
    --sky-mid:#4f9ad3;
    --sky-low:#c9e2f3;
    --sky-bottom:#eef6fb;
  }
  *{margin:0;padding:0;box-sizing:border-box}
  html,body{width:1200px;height:845px;overflow:hidden;background:var(--paper)}
  .cover-wrap{position:relative;width:1200px;height:845px;background:var(--paper);overflow:hidden}
  .mid-band{position:absolute;left:0;top:358px;width:1200px;height:309px;background:var(--band)}
  .spine-rule{position:absolute;top:0;width:1px;height:845px;background:var(--rule)}
  .spine-rule.left{left:563px}
  .spine-rule.right{left:637px}

  /* Back cover */
  .author-photo{position:absolute;left:69px;top:128px;width:160px;height:172px;border:3px solid var(--frame);
    background:linear-gradient(180deg,#ecebe4 0%,#e3e2dc 45%,#a9b3c6 75%,#7f8aa3 100%)}
  .back-title{position:absolute;left:240px;top:118px;font-family:"Roboto Condensed",sans-serif;font-weight:900;
    font-size:34px;letter-spacing:-0.3px;color:var(--ink);white-space:nowrap}
  .back-subtitle{position:absolute;left:240px;top:164px;font-family:"Roboto Condensed",sans-serif;font-weight:500;
    font-size:13px;line-height:15.7px;color:var(--accent-blue);white-space:nowrap}
  .reader-heading{position:absolute;left:83px;top:335px;font-family:"Source Sans 3",sans-serif;font-weight:700;
    font-size:12.2px;color:var(--ink)}
  .reader-list{position:absolute;left:83px;top:364px;list-style:none;font-family:"Source Sans 3",sans-serif;
    font-size:11.6px;line-height:14.1px;color:var(--ink)}
  .reader-list li{position:relative;white-space:nowrap}
  .reader-list li::before{content:"";position:absolute;left:-10px;top:3px;width:6px;height:6px;border-radius:50%;background:var(--accent-blue)}
  .back-copy{position:absolute;left:83px;font-family:"Source Sans 3",sans-serif;font-size:11.6px;line-height:14.1px;
    color:var(--ink);white-space:nowrap}
  .back-copy.first{top:576px}
  .back-copy.second{top:618px}

  /* Spine */
  .spine-text{position:absolute;left:582px;top:152px;writing-mode:vertical-rl;white-space:nowrap;display:flex;align-items:center}
  .spine-title{font-family:"Roboto",sans-serif;font-weight:300;font-size:30px;color:var(--spine-blue);margin-bottom:10px}
  .spine-author{font-family:"Roboto Condensed",sans-serif;font-weight:900;font-size:38px;color:var(--ink)}

  /* Front cover */
  .front-title{position:absolute;left:637px;width:563px;top:68px;text-align:center;font-family:"Roboto Condensed",sans-serif;
    font-weight:900;font-size:80px;letter-spacing:-0.5px;color:var(--ink);white-space:nowrap}
  .front-subtitle{position:absolute;left:637px;width:563px;top:170px;text-align:center;font-family:"Roboto Condensed",sans-serif;
    font-weight:500;font-size:23px;line-height:28.2px;color:var(--accent-blue);white-space:nowrap}
  .cover-art-frame{position:absolute;left:734px;top:312px;width:371px;height:400px;background:var(--frame);border-radius:4px;padding:6px}
  .cover-art{width:100%;height:100%;
    background:linear-gradient(180deg,var(--sky-top) 0%,var(--sky-mid) 40%,var(--sky-low) 72%,var(--sky-bottom) 100%)}
  .foreword{position:absolute;left:637px;width:563px;top:725px;text-align:center;font-family:"Roboto Condensed",sans-serif;
    font-weight:500;font-size:20px;color:var(--accent-blue)}
  .front-author{position:absolute;left:637px;width:563px;top:750px;text-align:center;font-family:"Roboto Condensed",sans-serif;
    font-weight:500;font-size:27px;color:var(--ink)}
</style>
</head>
<body>
<div class="cover-wrap">
  <div class="mid-band"></div>
  <div class="spine-rule left"></div>
  <div class="spine-rule right"></div>

  <!-- Back cover -->
  <section class="back-cover">
    <div class="author-photo" role="img" aria-label="Portrait photo of the author in a light grey blazer"></div>
    <h2 class="back-title">Steady Harbor</h2>
    <p class="back-subtitle">The secrets behind building a<br>multi-million dollar Insurance agency<br>Interviews, success stories and framework for success</p>
    <h3 class="reader-heading">Who should read this book?</h3>
    <ul class="reader-list">
      <li>Do you know that starting an Insurance Agency is probably one of<br>the best business ideas?</li>
      <li>Do you want to know how some startups created billion dollar<br>plus insurance based companies in the last 5-10 years?</li>
      <li>Do you want to know the secrets behind building a multi-million<br>dollar Insurance agency?</li>
      <li>Do you want to know how to scale up an Insurance Agency profitably?</li>
      <li>Do you want to know how to cut through the noise in the market<br>and differentiate your business?</li>
      <li>How to leverage technology to rise above (be seen and heard) the<br>myriad of agencies around you and compete with both local and<br>online agencies?</li>
      <li>How to build a team which carries your mindset to take care of cli-<br>ents and grow your business?</li>
    </ul>
    <p class="back-copy first">If you are interested in learning about these topics then you are at<br>the right place.</p>
    <p class="back-copy second">You can either spend years figuring out things yourself or read this<br>book and get wisdom from successful agents and thought leaders<br>at top insurance agencies."</p>
  </section>

  <!-- Spine -->
  <section class="spine-text">
    <span class="spine-title">Steady Harbor by</span>
    <span class="spine-author">Rudrank Bhalotia</span>
  </section>

  <!-- Front cover -->
  <section class="front-cover">
    <h1 class="front-title">Steady Harbor</h1>
    <p class="front-subtitle">The secrets behind building a<br>multi-million dollar Insurance agency<br>Interviews, success stories and framework for success</p>
    <div class="cover-art-frame">
      <div class="cover-art" role="img" aria-label="Illustration of a businessman with a briefcase walking into a blue sky with clouds, framed by two large open hands, paper planes flying above"></div>
    </div>
    <p class="foreword">Foreword by Milo Venhart</p>
    <p class="front-author">Rudrank Bhalotia</p>
  </section>
</div>
</body>
</html>
```